Construction company that specializes in roofing and siding

https://maplecrestbuild.example/featured-projects/

https://www.bramwickhomesllc.example/#

https://www.tallgrovecontractors.example/residential-siding-services/

Please model a website after these examples
I posted a doc that has some content to get you started. I will upload more content and photos as the site progresses.

Coded - Design and coding required

5+ page

```html
<!DOCTYPE html>
<html lang="en">
<head>
<meta charset="utf-8">
<title>Keystead Construction – Roofing &amp; Siding</title>
<link href="https://fonts.googleapis.com/css2?family=Rajdhani:wght@500;600;700&family=Inter:wght@400;500;600;700&display=swap" rel="stylesheet">
<style>
:root{
  --orange:#d9441c;
  --blue:#3b64c8;
  --ink:#1f1f22;
  --text:#3d3d42;
  --muted:#6b6b72;
  --dark:#1c1c1d;
  --card:#2a2a2f;
  --line:#e2e2e6;
  --panel:#e7e7e9;
  --white:#ffffff;
}
*{box-sizing:border-box;margin:0;padding:0}
html,body{width:1200px;height:4101px;overflow:hidden;background:var(--white)}
body{position:relative;font-family:'Inter',sans-serif;color:var(--text)}
.abs{position:absolute}
h1,h2,h3,.display{font-family:'Rajdhani',sans-serif}
.accent{color:var(--orange)}
svg{display:block}
a{color:inherit;text-decoration:none}

/* top bar */
.topbar{left:0;top:0;width:1200px;height:75px;background:var(--white)}
.brand-box{left:62px;top:0;width:212px;height:75px;background:var(--white);display:flex;align-items:center;gap:10px;padding-left:14px}
.brand-mark{width:30px;height:30px;border:3px solid #555;border-radius:50%}
.brand-name{font-family:'Rajdhani',sans-serif;font-weight:700;font-size:17px;line-height:1;color:#555;letter-spacing:.5px}
.contact{display:flex;align-items:center;gap:12px;font-size:11px;line-height:15px;color:var(--ink)}
.contact b{font-weight:600}
.btn{display:inline-flex;align-items:center;justify-content:center;gap:6px;background:var(--orange);color:var(--white);font-weight:600;font-size:13px;text-transform:uppercase;border-radius:3px}
.divider-v{left:632px;top:22px;width:1px;height:32px;background:var(--line)}

/* hero */
.hero{left:0;top:75px;width:1200px;height:480px;background:var(--blue)}
.hero-photo{left:540px;top:134px;width:660px;height:421px;background:linear-gradient(120deg,#3b64c8 0%,#5a6e9a 35%,#8a6a5a 70%,#6e4a3e 100%)}
.nav{left:62px;top:75px;width:1074px;height:59px;background:var(--white);display:flex;align-items:center;padding:0 32px;gap:22px;font-size:12px;font-weight:600;color:var(--ink);text-transform:uppercase}
.nav .active{color:var(--orange)}
.nav .caret::after{content:"▾";font-size:9px;margin-left:3px}
.socials{display:flex;gap:10px}
.social{width:29px;height:29px;border:1px solid var(--line);background:#f3f3f4;display:flex;align-items:center;justify-content:center}
.social i{width:10px;height:10px;background:var(--orange)}
.hero-title{left:60px;top:205px;font-size:42px;font-weight:700;line-height:52px;color:var(--white)}
.hero-text{left:62px;top:329px;width:500px;font-size:15px;line-height:19px;color:var(--white)}
.hero-dots{left:27px;top:290px}
.hero-dots span{display:block;width:9px;height:9px;border-radius:50%;background:#8ea4dc;margin-bottom:12px}
.hero-dots span.on{background:var(--white);border:2px solid var(--orange)}

/* booking */
.booking{left:172px;top:498px;width:856px;height:229px;background:var(--white);box-shadow:0 6px 28px rgba(0,0,0,.12);padding:26px 27px}
.booking h2{font-size:29px;font-weight:700;color:var(--ink);line-height:1}
.booking .note{font-size:11px;margin-top:10px;color:var(--ink)}
.booking .note em{color:var(--orange);font-style:normal}
.field{position:absolute;height:39px;border:1px solid var(--line);border-radius:3px;display:flex;align-items:center;justify-content:space-between;padding:0 13px;font-size:12px;color:#8a8a90}

/* about */
.about-photo{left:62px;top:823px;width:459px;height:503px;border-radius:14px;background:linear-gradient(160deg,#7d8a94 0%,#5b6f84 45%,#394656 100%)}
.dots-pattern{left:347px;top:791px;width:242px;height:284px;background-image:radial-gradient(#b9b9bf 1.3px,transparent 1.4px);background-size:10px 10px}
.stat{left:307px;top:1152px;width:283px;height:178px;background:var(--orange);border-radius:6px;color:var(--white);display:flex;align-items:center;gap:14px;padding-left:18px;border:8px solid var(--white)}
.stat .num{font-family:'Rajdhani',sans-serif;font-size:29px;font-weight:700;line-height:30px}
.stat .lbl{font-family:'Rajdhani',sans-serif;font-size:19px;line-height:23px}
.about-title{left:608px;top:816px;font-size:36px;font-weight:500;line-height:44px;color:var(--ink)}
.about-title b{font-weight:700;color:var(--orange)}
.para{font-size:13.5px;line-height:19px;color:var(--text)}
.feature{display:flex;gap:12px;align-items:center;font-size:15px;line-height:21px;color:var(--ink)}

/* services */
.services{left:0;top:1415px;width:1200px;height:681px;background:var(--dark)}
.services-title{left:0;top:1476px;width:1200px;text-align:center;font-size:36px;font-weight:500;color:var(--white)}
.services-title b{font-weight:700}
.svc{position:absolute;top:1574px;width:342px;height:399px;background:var(--card);border-radius:10px;overflow:hidden}
.svc .img{height:228px}
.svc h3{font-family:'Inter',sans-serif;font-size:16px;font-weight:700;color:var(--white);margin:22px 13px 11px}
.svc p{font-size:12px;line-height:17px;color:#9a9aa2;margin:0 13px;padding-bottom:14px;border-bottom:1px solid #3a3a40}
.svc .more{display:flex;align-items:center;gap:6px;font-size:12px;font-weight:600;color:var(--white);margin:20px 13px 0}
.pager{display:flex;gap:8px}
.pager span{width:18px;height:5px;border-radius:3px;background:#55555c}
.pager span.on{background:var(--orange)}
.pager.light span{background:#c9c9cf}
.pager.light span.on{background:var(--orange)}

/* promise */
.promise-house{left:620px;top:2136px;width:580px;height:400px;background:linear-gradient(90deg,rgba(236,238,244,0) 0%,#eef0f5 40%,#e6e9f0 100%)}
.promise-person{left:32px;top:2136px;width:305px;height:400px;background:linear-gradient(180deg,#f0f0f2 0%,#e58a3a 45%,#c86a2a 70%,#5c7aa5 100%);border-radius:4px}
.promise-title{left:347px;top:2218px;font-size:35px;font-weight:500;color:var(--ink)}
.promise-title b{font-weight:700;color:var(--orange)}
.promise-text{left:349px;top:2272px;width:530px;font-size:16.5px;line-height:22px;color:var(--ink)}
.signoff{left:657px;top:2375px;font-size:17px;line-height:24px;color:var(--ink)}

/* gallery */
.gal-title{left:62px;top:2604px;font-size:36px;font-weight:500;line-height:44px;color:var(--ink)}
.gal-title b{font-weight:700;color:var(--orange)}
.arrow-btn{position:absolute;top:2655px;width:34px;height:32px;background:var(--orange);border-radius:3px;display:flex;align-items:center;justify-content:center}
.tile{position:absolute;top:2712px;width:300px;height:420px}
.tile-caption{left:20px;top:3060px;color:var(--white)}
.tile-caption h3{font-family:'Inter',sans-serif;font-size:16px;font-weight:700}
.tile-caption div{display:flex;align-items:center;gap:8px;font-size:13px;font-weight:600;margin-top:10px}

/* testimonials */
.testi-title{left:0;top:3196px;width:1200px;text-align:center;font-size:35px;font-weight:500;color:var(--ink)}
.quote{position:absolute;top:3310px;width:528px;height:215px;background:var(--panel);border-radius:14px;padding:40px 32px}
.quote p{font-size:13.5px;line-height:18px;color:var(--text);margin-top:14px}
.quote .tail{position:absolute;left:70px;bottom:-18px;width:0;height:0;border-left:18px solid transparent;border-right:18px solid transparent;border-top:18px solid var(--panel)}
.person{position:absolute;top:3568px;display:flex;align-items:center;gap:18px}
.avatar{width:62px;height:62px;border-radius:50%;background:linear-gradient(135deg,#c9a98a,#6d5a4a)}
.person h3{font-family:'Inter',sans-serif;font-size:19px;font-weight:700;color:var(--ink)}
.person span{font-size:13.5px;color:var(--muted)}

/* footer */
.footer{left:0;top:3745px;width:1200px;height:356px;background:var(--dark);color:#d8d8dc}
.footer h4{font-family:'Inter',sans-serif;font-size:17px;font-weight:600;color:var(--white);margin-bottom:10px}
.footer h4::after{content:"";display:block;width:24px;height:2px;background:var(--orange);margin-top:8px}
.fcol{position:absolute;top:3793px;font-size:12.5px;line-height:22px}
.fcol .dim{color:#8a8a92}
.fsocial{display:flex;gap:18px}
.fsocial i{width:10px;height:10px;background:var(--orange)}
.frule{left:0;top:4045px;width:1200px;height:1px;background:#333}
.copy{left:0;top:4060px;width:1200px;text-align:center;font-size:12.5px;color:#d8d8dc}
</style>
</head>
<body>

<!-- header -->
<header>
  <div class="abs topbar"></div>
  <div class="abs brand-box"><span class="brand-mark"></span><span class="brand-name">KEYSTEAD<br>CONSTRUCTION</span></div>
  <div class="abs contact" style="left:417px;top:22px">
    <svg width="16" height="20" viewBox="0 0 16 20"><path d="M8 0a7 7 0 0 0-7 7c0 5 7 13 7 13s7-8 7-13a7 7 0 0 0-7-7zm0 10a3 3 0 1 1 0-6 3 3 0 0 1 0 6z" fill="#d9441c"/></svg>
    <div><b>Address:</b><br>48 Alder Bend Rd. Fairhaven</div>
  </div>
  <div class="abs divider-v"></div>
  <div class="abs contact" style="left:660px;top:22px">
    <svg width="20" height="20" viewBox="0 0 24 24"><path d="M6.6 10.8a15 15 0 0 0 6.6 6.6l2.2-2.2a1 1 0 0 1 1-.25 11.4 11.4 0 0 0 3.6.57 1 1 0 0 1 1 1V20a1 1 0 0 1-1 1A17 17 0 0 1 3 4a1 1 0 0 1 1-1h3.5a1 1 0 0 1 1 1c0 1.25.2 2.45.57 3.57a1 1 0 0 1-.25 1z" fill="#d9441c"/></svg>
    <div><b>Call Us:</b><br>1800-5550-2417</div>
  </div>
  <a class="abs btn" style="left:947px;top:16px;width:189px;height:41px">Make Appointment</a>
</header>

<!-- hero -->
<section>
  <div class="abs hero"></div>
  <div class="abs hero-photo" role="img" aria-label="Roofers laying underlayment rolls on a shingled roof"></div>
  <nav class="abs nav">
    <span class="active">Home</span><span>About</span><span class="caret">Roofing</span><span class="caret">Siding</span><span>Gutters</span><span class="caret">Repair</span><span>Storm Damage Repair</span>
    <div class="socials" style="margin-left:auto"><span class="social"><i></i></span><span class="social"><i></i></span><span class="social"><i></i></span><span class="social"><i></i></span></div>
  </nav>
  <div class="abs hero-dots"><span></span><span class="on"></span><span></span></div>
  <h1 class="abs hero-title">Lorem Ipsum is simply<br>dummy text of the printing</h1>
  <p class="abs hero-text">Lorem Ipsum is simply dummy text of the printing and typesetting industry. Lorem Ipsum has been the industry's standard</p>
  <a class="abs btn" style="left:62px;top:392px;width:123px;height:36px">Read More
    <svg width="10" height="10" viewBox="0 0 10 10"><path d="M3 1l4 4-4 4" stroke="#fff" stroke-width="2" fill="none"/></svg></a>
</section>

<!-- booking -->
<section class="abs booking">
  <h2>Book Roofing <span class="accent">Inspection</span></h2>
  <p class="note"><em>*</em>Your roof will require some professional attention for long live.</p>
  <div class="field" style="left:27px;top:104px;width:255px">Name
    <svg width="14" height="14" viewBox="0 0 16 16"><circle cx="8" cy="5" r="3.2" stroke="#d9441c" stroke-width="1.4" fill="none"/><path d="M2 15c0-3.3 2.7-5.5 6-5.5s6 2.2 6 5.5" stroke="#d9441c" stroke-width="1.4" fill="none"/></svg></div>
  <div class="field" style="left:301px;top:104px;width:254px">Phone
    <svg width="14" height="14" viewBox="0 0 24 24"><path d="M6.6 10.8a15 15 0 0 0 6.6 6.6l2.2-2.2 4.6 1.4V20A17 17 0 0 1 3 4h3.5l1.4 4.6z" stroke="#d9441c" stroke-width="2" fill="none"/></svg></div>
  <div class="field" style="left:574px;top:104px;width:254px">Email
    <svg width="15" height="12" viewBox="0 0 16 12"><rect x="1" y="1" width="14" height="10" stroke="#d9441c" stroke-width="1.4" fill="none"/><path d="M1 1l7 6 7-6" stroke="#d9441c" stroke-width="1.4" fill="none"/></svg></div>
  <div class="field" style="left:27px;top:162px;width:255px">dd/mm/yyyy
    <svg width="14" height="14" viewBox="0 0 16 16"><rect x="1" y="3" width="14" height="12" stroke="#d9441c" stroke-width="1.4" fill="none"/><path d="M1 7h14M5 1v4M11 1v4" stroke="#d9441c" stroke-width="1.4"/></svg></div>
  <div class="field" style="left:301px;top:162px;width:254px">Location
    <svg width="12" height="15" viewBox="0 0 16 20"><path d="M8 1a6 6 0 0 0-6 6c0 4.5 6 12 6 12s6-7.5 6-12a6 6 0 0 0-6-6z" stroke="#d9441c" stroke-width="1.6" fill="none"/><circle cx="8" cy="7" r="2" fill="#d9441c"/></svg></div>
  <a class="btn" style="position:absolute;left:574px;top:162px;width:254px;height:39px">Book for Inspection</a>
</section>

<!-- about -->
<section>
  <div class="abs dots-pattern"></div>
  <div class="abs about-photo" role="img" aria-label="Roofer in safety vest and sunglasses nailing shingles"></div>
  <div class="abs stat">
    <svg width="62" height="56" viewBox="0 0 62 56"><path d="M4 26L31 4l27 22M10 22v30h42V22" stroke="#fff" stroke-width="2.5" fill="none"/><rect x="16" y="30" width="10" height="10" stroke="#fff" stroke-width="2" fill="none"/><rect x="34" y="30" width="12" height="22" stroke="#fff" stroke-width="2" fill="none"/></svg>
    <div><div class="num">2009+</div><div class="lbl">Residential Projects<br>Completed</div></div>
  </div>
  <h2 class="abs about-title">Lorem Ipsum is simply dummy<br>text <b>of the printing</b></h2>
  <p class="abs para" style="left:609px;top:930px;width:530px">Lorem Ipsum is simply dummy text of the printing and typesetting industry. Lorem Ipsum has been the industry's standard dummy text ever since the 1500s, when an unknown printer took a galley of type and scrambled it to make a type specimen book. It has survived not only five centuries, but also the leap into electronic typesetting.</p>
  <div class="abs feature" style="left:610px;top:1064px">
    <svg width="46" height="38" viewBox="0 0 46 38"><path d="M2 36h34M6 36V20l14-12 14 12v16M12 26h6v10M24 26h6v4" stroke="#d9441c" stroke-width="2" fill="none"/><path d="M30 8l12-6 2 4-12 6z" stroke="#d9441c" stroke-width="2" fill="none"/></svg>
    <span>Lorem Ipsum is simply<br>dummy text of the</span></div>
  <div class="abs feature" style="left:895px;top:1064px">
    <svg width="40" height="38" viewBox="0 0 40 38"><path d="M2 36h36M6 36V14h14v22M24 36V6h10v30M10 20h6M10 26h6M27 12h4M27 18h4M27 24h4" stroke="#d9441c" stroke-width="2" fill="none"/></svg>
    <span>Lorem Ipsum is simply<br>dummy text of the</span></div>
  <p class="abs para" style="left:609px;top:1142px;width:530px">Lorem Ipsum is simply dummy text of the printing and typesetting industry. Lorem Ipsum has been the industry's standard dummy text ever since the 1500s, when an unknown printer took a galley of type and scrambled it to make a type specimen book.</p>
  <a class="abs btn" style="left:608px;top:1254px;width:111px;height:40px">Read More</a>
</section>

<!-- services -->
<section>
  <div class="abs services"></div>
  <h2 class="abs services-title">We Provide <b>Superior Services</b></h2>
  <article class="svc" style="left:62px">
    <div class="img" role="img" aria-label="Architectural sketch of a house with shingled roof" style="background:linear-gradient(135deg,#eef0f8,#b9c3ea)"></div>
    <h3>Architectural shingles</h3>
    <p>Lorem Ipsum is simply dummy text of the printing and typesetting industry. Lorem Ipsum has been the industry's standard dummy</p>
    <div class="more">Read More <svg width="10" height="10" viewBox="0 0 10 10"><path d="M1 5h7M5 2l3 3-3 3" stroke="#fff" stroke-width="1.6" fill="none"/></svg></div>
  </article>
  <article class="svc" style="left:428px">
    <div class="img" role="img" aria-label="Worker installing vinyl siding panels" style="background:linear-gradient(135deg,#2c3e6a,#9aa4b0 60%,#dcdcd6)"></div>
    <h3>Vinyl siding</h3>
    <p>Lorem Ipsum is simply dummy text of the printing and typesetting industry. Lorem Ipsum has been the industry's standard dummy</p>
    <div class="more">Read More <svg width="10" height="10" viewBox="0 0 10 10"><path d="M1 5h7M5 2l3 3-3 3" stroke="#fff" stroke-width="1.6" fill="none"/></svg></div>
  </article>
  <article class="svc" style="left:794px">
    <div class="img" role="img" aria-label="Roofer repairing red clay tile roof" style="background:linear-gradient(180deg,#dfe6ee 0%,#b4472f 55%,#8a3422 100%)"></div>
    <h3>Leaking roof</h3>
    <p>Lorem Ipsum is simply dummy text of the printing and typesetting industry. Lorem Ipsum has been the industry's standard dummy</p>
    <div class="more">Read More <svg width="10" height="10" viewBox="0 0 10 10"><path d="M1 5h7M5 2l3 3-3 3" stroke="#fff" stroke-width="1.6" fill="none"/></svg></div>
  </article>
  <div class="abs pager" style="left:564px;top:2016px"><span class="on"></span><span></span><span></span></div>
</section>

<!-- promise -->
<section>
  <div class="abs promise-house" role="img" aria-label="Faint line sketch of a house"></div>
  <div class="abs promise-person" role="img" aria-label="Smiling contractor in hard hat and safety vest holding a tablet"></div>
  <h2 class="abs promise-title">The Keystead <b>Promise</b></h2>
  <p class="abs promise-text">You deserve timely service, high quality materials, expert installation, and an ironclad warranty. That is what we promise to deliver. I invite you to put us to the test today.</p>
  <div class="abs signoff"><b><i>Sincerely,</i></b><br><b>Dale Marsh, Owner</b><br>&nbsp;Keystead Construction</div>
</section>

<!-- gallery -->
<section>
  <h2 class="abs gal-title">Inspiration on Your<br><b>Next Project</b></h2>
  <div class="arrow-btn" style="left:1057px"><svg width="10" height="12" viewBox="0 0 10 12"><path d="M7 1L2 6l5 5" stroke="#fff" stroke-width="2" fill="none"/></svg></div>
  <div class="arrow-btn" style="left:1102px"><svg width="10" height="12" viewBox="0 0 10 12"><path d="M3 1l5 5-5 5" stroke="#fff" stroke-width="2" fill="none"/></svg></div>
  <div class="tile" role="img" aria-label="Roofer working beside a brick chimney" style="left:0;background:linear-gradient(180deg,#cfd8e4 0%,#6a6a74 55%,#2b2b30 100%)"></div>
  <div class="tile" role="img" aria-label="Nail gun fastening roof shingles" style="left:300px;background:linear-gradient(160deg,#2e3a5c,#6c7690 55%,#a8aab2)"></div>
  <div class="tile" role="img" aria-label="Hammer driving nails into wooden shakes" style="left:600px;background:linear-gradient(160deg,#b06a3e,#6a4a3a 50%,#3a3d44)"></div>
  <div class="tile" role="img" aria-label="Smiling contractor in hard hat on a roof" style="left:900px;background:linear-gradient(180deg,#e8ebf0 0%,#c9c7c2 45%,#d98a3a 100%)"></div>
  <div class="abs tile-caption"><h3>Lorem Ipsum is simply</h3>
    <div><svg width="12" height="12" viewBox="0 0 12 12"><circle cx="6" cy="6" r="5" stroke="#d9441c" stroke-width="1.6" fill="none"/><circle cx="6" cy="6" r="2" fill="#d9441c"/></svg>VIEW MORE</div></div>
</section>

<!-- testimonials -->
<section>
  <h2 class="abs testi-title">Testimonials</h2>
  <div class="quote" style="left:62px">
    <svg width="22" height="16" viewBox="0 0 22 16"><path d="M0 16V8l5-8h4L6 7h4v9zM12 16V8l5-8h4l-3 7h4v9z" fill="#d9441c"/></svg>
    <p>Lorem Ipsum is simply dummy text of the printing and typesetting industry. Lorem Ipsum has been the industry's standard dummy text ever since the 1500s, when an unknown printer took a galley of type and scrambled it to make a type specimen book. It has survived not only five centuries, but also the leap into electronic</p>
    <svg style="position:absolute;right:62px;bottom:28px" width="22" height="16" viewBox="0 0 22 16"><path d="M22 0v8l-5 8h-4l3-7h-4V0zM10 0v8l-5 8H1l3-7H0V0z" fill="#d9441c"/></svg>
    <span class="tail"></span>
  </div>
  <div class="quote" style="left:609px">
    <svg width="22" height="16" viewBox="0 0 22 16"><path d="M0 16V8l5-8h4L6 7h4v9zM12 16V8l5-8h4l-3 7h4v9z" fill="#d9441c"/></svg>
    <p>Lorem Ipsum is simply dummy text of the printing and typesetting industry. Lorem Ipsum has been the industry's standard dummy text ever since the 1500s, when an unknown printer took a galley of type and scrambled it to make a type specimen book. It has survived not only five centuries, but also the leap into electronic</p>
    <svg style="position:absolute;right:62px;bottom:28px" width="22" height="16" viewBox="0 0 22 16"><path d="M22 0v8l-5 8h-4l3-7h-4V0zM10 0v8l-5 8H1l3-7H0V0z" fill="#d9441c"/></svg>
    <span class="tail"></span>
  </div>
  <div class="person" style="left:116px"><div class="avatar" role="img" aria-label="Customer portrait"></div><div><h3>Owen Pratt</h3><span>Managing Diretor</span></div></div>
  <div class="person" style="left:662px"><div class="avatar" role="img" aria-label="Customer portrait" style="background:linear-gradient(135deg,#3a6ac8,#d98a3a)"></div><div><h3>Ned Farrow</h3><span>Customer Service Is Exeeellent</span></div></div>
  <div class="abs pager light" style="left:564px;top:3674px"><span class="on"></span><span></span><span></span></div>
</section>

<!-- footer -->
<footer>
  <div class="abs footer"></div>
  <div class="fcol" style="left:62px;top:3805px;width:270px">
    <div style="display:flex;align-items:center;gap:10px;margin-bottom:18px"><span class="brand-mark" style="border-color:#fff"></span><span class="brand-name" style="color:#fff">KEYSTEAD<br>CONSTRUCTION</span></div>
    <p style="font-size:12px;line-height:16px">Lorem Ipsum is simply dummy text of the printing and typesetting industry. Lorem Ipsum has been the industry's standard</p>
    <div class="fsocial" style="margin-top:28px"><i></i><i></i><i></i><i></i></div>
  </div>
  <div class="fcol" style="left:366px"><h4>Information</h4>Home<br>About<br>Roofing<br>Siding<br>Gutters<br>Repair<br>Storm damage repair</div>
  <div class="fcol" style="left:559px"><h4>Our Link</h4>Help<br>Support<br>Clients<br>Contacts</div>
  <div class="fcol" style="left:713px"><h4>Time</h4>Monday: <span class="dim">10.00AM - 4.00PM</span><br>Tuesday: <span class="dim">10.00AM - 4.00PM</span><br>Wednesday: <span class="dim">10.00AM - 4.00PM</span><br>Thursday: <span class="dim">10.00AM - 4.00PM</span><br>Friday: <span class="dim">Close</span></div>
  <div class="fcol" style="left:941px;font-size:12px"><h4>Get in Touch</h4>
    <div style="display:flex;gap:8px;align-items:center"><svg width="10" height="10" viewBox="0 0 24 24"><path d="M6.6 10.8a15 15 0 0 0 6.6 6.6l2.2-2.2 5.6 1.4V21A18 18 0 0 1 3 3h4.4l1.4 5.6z" fill="#d9441c"/></svg>1800-5550-2417</div>
    <div style="display:flex;gap:8px;align-items:center;margin-top:8px"><svg width="11" height="9" viewBox="0 0 16 12"><rect x="1" y="1" width="14" height="10" stroke="#d9441c" stroke-width="2" fill="none"/><path d="M1 1l7 6 7-6" stroke="#d9441c" stroke-width="2" fill="none"/></svg>info@keysteadbuild.example</div>
    <div style="display:flex;gap:8px;align-items:flex-start;margin-top:8px"><svg width="10" height="13" viewBox="0 0 16 20" style="margin-top:5px"><path d="M8 0a7 7 0 0 0-7 7c0 5 7 13 7 13s7-8 7-13a7 7 0 0 0-7-7z" fill="#d9441c"/></svg>48 Alder Bend Rd.<br>Fairhaven</div>
  </div>
  <div class="abs frule"></div>
  <p class="abs copy">© Copyright 2024 Keystead Construction-All rights reserved.</p>
</footer>

</body>
</html>
```